Brightmill Data Works

Our company is about IT hardwares and IT solutions. IT hardware such as PC, RAMS, storage and servers. IT solutions such as project management, BA. We are also selling new technology too.

Target Market(s)

Consumer, Small to Medium Business, Corporate

Requirements
Must have
• The business card must have the following:
• Name:
• Title:
• Contact Number:
• Email address:
• Website:
• Color: Must match the logo color upgrade

```html
<!DOCTYPE html>
<html lang="en">
<head>
<meta charset="UTF-8">
<title>Brightmill Data Works – Business Card</title>
<link rel="stylesheet" href="https://fonts.googleapis.com/css2?family=Russo+One&family=Arimo:wght@400;700&display=swap">
<style>
  :root {
    --stage: #262628;
    --card-dark: #434343;
    --card-white: #ffffff;
    --copper: #c8762e;
    --copper-deep: #b0621f;
    --ink: #4a4a4a;
    --text-light: #f2f2f2;
  }
  * { box-sizing: border-box; margin: 0; padding: 0; }
  html, body {
    width: 1200px; height: 800px; overflow: hidden;
    background: var(--stage);
  }
  .stage {
    position: relative; width: 1200px; height: 800px;
    display: flex; align-items: center; justify-content: center; gap: 40px;
  }
  .card {
    position: relative; width: 540px; height: 309px; overflow: hidden;
    box-shadow: 0 18px 40px rgba(0,0,0,.45);
  }
  .card--back { background: var(--card-dark); }
  .card--front { background: var(--card-white); }
  .card__art { position: absolute; inset: 0; width: 100%; height: 100%; }

  .wordmark {
    position: absolute; display: flex; align-items: center; gap: 12px;
    font-family: "Russo One", sans-serif; text-transform: uppercase;
    letter-spacing: 1px; line-height: 1.05;
  }
  .wordmark__square { width: 16px; height: 16px; background: var(--copper); flex: none; }
  .wordmark__name { font-size: 27px; }
  .card--back .wordmark { left: 50%; top: 50%; transform: translate(-50%, -50%); }
  .card--back .wordmark__name { color: var(--text-light); }
  .card--front .wordmark { left: 58px; top: 82px; }
  .card--front .wordmark__name { color: var(--ink); font-size: 24px; }

  .contact {
    position: absolute; right: 22px; top: 118px; text-align: right;
    font-family: "Arimo", sans-serif; color: var(--text-light);
    font-size: 10.5px; line-height: 1.38;
  }
  .contact__name { font-weight: 700; font-size: 12.5px; letter-spacing: .3px; line-height: 1.1; }
  .contact__title { font-size: 10.5px; margin-bottom: 8px; }
  .contact__address { margin-bottom: 3px; }
  .contact__line { display: flex; justify-content: flex-end; align-items: center; gap: 5px; }
  .contact__icon { width: 9px; height: 9px; fill: var(--text-light); flex: none; }
</style>
</head>
<body>
<main class="stage">

  <section class="card card--back" aria-label="Card back">
    <div class="wordmark">
      <span class="wordmark__square"></span>
      <span class="wordmark__name">Brightmill<br>Data Works</span>
    </div>
  </section>

  <section class="card card--front" aria-label="Card front">
    <svg class="card__art" viewBox="0 0 540 309" preserveAspectRatio="none" aria-hidden="true">
      <defs>
        <linearGradient id="copperSweep" x1="1" y1="0" x2="0" y2="1">
          <stop offset="0" stop-color="#d58a3e"/>
          <stop offset="1" stop-color="#b0621f"/>
        </linearGradient>
      </defs>
      <path d="M518,0 C470,100 130,205 0,218 L0,292 C140,245 494,88 531,0 Z" fill="url(#copperSweep)"/>
      <path d="M537,0 C500,90 150,250 10,309 L540,309 L540,0 Z" fill="var(--card-dark)"/>
    </svg>

    <div class="wordmark">
      <span class="wordmark__square"></span>
      <span class="wordmark__name">Brightmill<br>Data Works</span>
    </div>

    <div class="contact">
      <p class="contact__name">DANIEL REYES</p>
      <p class="contact__title">Manager</p>
      <p class="contact__address">PO Box 48 Harbor Lane<br>2nd Street Carlton</p>
      <p class="contact__line">555-214-0387
        <svg class="contact__icon" viewBox="0 0 24 24"><path d="M6.6 10.8a15.1 15.1 0 0 0 6.6 6.6l2.2-2.2c.3-.3.7-.4 1-.2 1.1.4 2.300.6 3.6.6.6 0 1 .4 1 1V20c0 .6-.4 1-1 1A17 17 0 0 1 3 4c0-.6.4-1 1-1h3.5c.6 0 1 .4 1 1 0 1.3.2 2.5.6 3.6.1.3 0 .7-.2 1z"/></svg>
      </p>
      <p class="contact__line">info@brightmilldata.com
        <svg class="contact__icon" viewBox="0 0 24 24"><path d="M2 5h20v14H2z M4 7v.5l8 5 8-5V7z" fill-rule="evenodd"/></svg>
      </p>
      <p class="contact__line">www.brightmilldata.com
        <svg class="contact__icon" viewBox="0 0 24 24"><path d="M12 2a10 10 0 1 0 0 20 10 10 0 0 0 0-20zm0 2c.9 1.1 1.7 2.8 2 5h-4c.3-2.2 1.1-3.9 2-5zM4.3 11h3.8c.1 1.4.2 2.7.6 4H5.2a8 8 0 0 1-.9-4zm5.8 0h3.8a15 15 0 0 1-.5 4h-2.8c-.3-1.3-.5-2.6-.5-4zm5.8 0h3.8a8 8 0 0 1-.9 4h-3.5c.4-1.3.5-2.6.6-4zM5.2 9a8 8 0 0 1 3.6-4c-.5 1.1-.8 2.5-.9 4zm10.9 0c-.1-1.5-.4-2.9-.9-4a8 8 0 0 1 3.6 4zM6.3 17h2.9c.3.9.6 1.6 1 2.3A8 8 0 0 1 6.3 17zm4.9 0h1.6l-.8 1.8zm3.6 0h2.9a8 8 0 0 1-3.9 2.3c.4-.7.7-1.400 1-2.3z"/></svg>
      </p>
    </div>
  </section>

</main>
</body>
</html>
```